Interior Design for Every Day, Nora Whitfield Interior Design, LLC

We are looking for a website for an Interior Design Company targeted at higher income households. We prefer to work with clients that seek to amplify the architectural beauty of their interior space via interior design - while ensuring the space promotes easy living. For example: a kitchen should be lain out in an intuitive manner such that all utensils, cups and plates are easy to find. Living rooms should be arranged to promote conversation and/or watch TV, etc.... We have heavy reliance on the technical aspects of design (computer automated renderings). We like the look and feel of this website: https://www.brenthalvorsen.example/portfolioall

Target Market(s)

Upper HHI ($200,000+) in the Atlanta Metro Market. Customers are likely to be highly educated and from a variety of cultural backgrounds. Ages 35-60

Industry/Entity Type

Architecture

Font styles to use
Sans Serif

Colors

Designer to choose colors to be used in the design.

Requirements
Must have
• Landing Page, Page demonstrating how interior design fits into the architectural design process, About Us Page with contact info, Example Work Page and Tailored Client Page. Minimal work can be done on the About Us and example work pages. The tailored client page just needs a good layout (and easy uploads and download capability)
• Also to include:
• (1) The landing page should include a Design Philosophy Section and maybe a couple examples of our work and/or pictures you provide
• (2) The Design Process page should explain all steps of the architectural Design process and should explain where interior design/decorating fits into the Architectural process (see below attachments).
• (3) The Example work page should include areas for portfolio example uploads (to include 3 dimensional and 2 dimensional renderings, photos and videos).
• (4) Include a Password Protected, Secure Place where each individual client can store and retrieve documents and work product for their project (Should be a separate page). There should be sections (for each client) for:
• (a) there should be a client account creation requirement page that requires: FN, LN, Mobile, email, Work phone, Property address, City, Zip (for 3 properties), Spouse FN, Spouse LN, Child FN, LN (space for 5 children)
• (a) section: Legal & Invoices
• (b) section: Drawings & Renderings
• (c) section: Pin Ups (easy uploads of pictures from sites like snapboardia would be appreciated) - pin ups should be very easy for clients to put examples of what they like
• (5) Ability for admin to use personalized password and username to view, delete and edit client files (we utilize filecrate for document storage currently, and integration with filecrate would be a plus)
• (6) needs to be formatted and optimized for Mobile (iOs and android) viewing as well as Web
• (7) The site should be built with a hosting service contemplated. This service should be affordable (Less than $300 per annum)
• (8) most importantly the site should be minimalist with focus on user friendliness while being fashion forward
• (9) Website Color scheme should be White/Black/BlueGrey
• (10) The site must also include the ability to generate an invoice, based on client registration, electronically submit the invoice to the client via email (or print it), accept payment via coinvoy integration, and generate conformation email of payment to both client and admin (although coinvoy may already do this).
Nice to have
• Ability of example and client pages to be integrated with sites like snapbordia and filecrate. Ability to have some sort of section that self identifies the clients design style(s)...maybe a quiz or at lease a place where they can create a pinboard of images and colors they like (potentially by room)
Should not have
• Must look modern and be extremely quick/user friendly. Our clients are very busy.

```html
<!DOCTYPE html>
<html lang="en">
<head>
<meta charset="utf-8">
<title>Nora Whitfield Interior Design</title>
<link href="https://fonts.googleapis.com/css2?family=Roboto+Condensed:wght@400;700&family=Roboto:wght@400&family=Open+Sans:wght@400&display=swap" rel="stylesheet">
<style>
  :root {
    --accent: #5a7291;
    --ink: #2b2b2b;
    --muted: #555;
    --paper: #ffffff;
    --band: #f1f1f2;
    --footer: #232323;
    --hero-dark: #2a2b2d;
    --hero-light: #6d6a66;
    --card-line: #e0e0e0;
  }
  * { box-sizing: border-box; margin: 0; padding: 0; }
  html, body { width: 889px; height: 1200px; overflow: hidden; background: var(--paper); }
  .page { position: relative; width: 889px; height: 1200px; font-family: 'Open Sans', sans-serif; color: var(--ink); }

  .site-nav { position: absolute; top: 0; left: 0; width: 889px; height: 36px; background: var(--paper); border-top: 1px solid #ddd; }
  .site-nav a { position: absolute; top: 11px; font-family: 'Roboto', sans-serif; font-size: 11.5px; color: #555; text-decoration: none; letter-spacing: 0.1px; }
  .site-nav a.is-current { color: var(--accent); }
  .nav-sep { position: absolute; top: 12px; width: 1px; height: 11px; background: #ccc; }

  .hero { position: absolute; top: 36px; left: 0; width: 889px; height: 402px; }
  .hero-photo { position: absolute; inset: 0; background: linear-gradient(100deg, #3a3633 0%, var(--hero-dark) 35%, var(--hero-light) 70%, #4d4c4a 100%); }
  .hero-copy { position: absolute; left: 554px; top: 150px; color: #fff; font-family: 'Roboto Condensed', sans-serif; }
  .hero-title { font-weight: 700; font-size: 37px; line-height: 40px; }
  .hero-sub { font-weight: 700; font-size: 30px; line-height: 34px; margin-top: 2px; }
  .hero-tagline { font-family: 'Roboto', sans-serif; font-size: 11.5px; line-height: 16px; margin-top: 12px; }
  .hero-arrow { position: absolute; top: 214px; width: 26px; height: 26px; }

  .welcome { position: absolute; top: 438px; left: 0; width: 889px; height: 251px; background: var(--band); text-align: center; }
  .welcome-title { position: absolute; top: 50px; width: 100%; font-family: 'Roboto Condensed', sans-serif; font-weight: 400; font-size: 26px; color: #333; }
  .welcome-title span { color: var(--accent); }
  .welcome-divider { position: absolute; top: 88px; left: 350px; }
  .welcome-text { position: absolute; top: 117px; left: 118px; width: 653px; font-size: 8.4px; line-height: 15.3px; color: var(--muted); }
  .btn-more { position: absolute; top: 180px; left: 388px; width: 92px; height: 26px; border-radius: 13px; background: var(--accent); color: #fff; font-family: 'Roboto Condensed', sans-serif; font-size: 11.5px; line-height: 26px; }

  .work-title { position: absolute; top: 735px; width: 889px; text-align: center; font-family: 'Roboto Condensed', sans-serif; font-size: 26px; color: #222; }
  .work-card { position: absolute; top: 795px; width: 175px; height: 198px; background: #fff; border: 1px solid var(--card-line); border-bottom: 2px solid #d6d6d6; }
  .work-card .render { height: 144px; }
  .work-card p { padding: 12px 8px 0; text-align: center; font-size: 8.3px; line-height: 14px; color: var(--muted); }

  .site-footer { position: absolute; top: 1053px; left: 0; width: 889px; height: 147px; background: var(--footer); color: #fff; text-align: center; }
  .social { position: absolute; top: 39px; left: 380px; display: flex; gap: 9.5px; }
  .social span { width: 18px; height: 18px; border-radius: 3px; background: #fff; display: block; }
  .footer-links { position: absolute; top: 70px; width: 100%; font-size: 10.4px; }
  .footer-links a { color: #fff; text-decoration: none; }
  .footer-links i { font-style: normal; margin: 0 6px; }
  .copyright { position: absolute; top: 94px; width: 100%; font-size: 9px; }
</style>
</head>
<body>
<div class="page">
  <nav class="site-nav">
    <a class="is-current" style="left:74px">HOME</a>
    <span class="nav-sep" style="left:118px"></span>
    <a style="left:146px">PROCESS</a>
    <span class="nav-sep" style="left:218px"></span>
    <a style="left:235px">ABOUT US</a>
    <span class="nav-sep" style="left:310px"></span>
    <a style="left:329px">EXAMPLE WORKS</a>
    <span class="nav-sep" style="left:442px"></span>
    <a style="left:462px">CLIENT CORNER</a>
    <span class="nav-sep" style="left:570px"></span>
    <a style="left:586px">CONTACT US</a>
  </nav>

  <header class="hero">
    <div class="hero-photo" role="img" aria-label="Modern open living room with dark sofa, dining table and large windows onto a terrace"></div>
    <svg class="hero-arrow" style="left:27px" viewBox="0 0 26 26" aria-hidden="true"><circle cx="13" cy="13" r="13" fill="#111"/><path d="M15 8 L10 13 L15 18" fill="none" stroke="#fff" stroke-width="2"/></svg>
    <svg class="hero-arrow" style="left:840px" viewBox="0 0 26 26" aria-hidden="true"><circle cx="13" cy="13" r="13" fill="#111"/><path d="M11 8 L16 13 L11 18" fill="none" stroke="#fff" stroke-width="2"/></svg>
    <div class="hero-copy">
      <div class="hero-title">NORA WHITFIELD</div>
      <div class="hero-sub">INTERIOR DESIGN</div>
      <div class="hero-tagline">INTERIOR DESIGN IS MAKING THE BEST POSSIBLE<br>USE OF THE AVAILABLE SPACE</div>
    </div>
  </header>

  <section class="welcome">
    <h1 class="welcome-title">WELCOME TO <span>NORA WHITFIELD INTERIOR DESIGN</span></h1>
    <svg class="welcome-divider" width="178" height="16" viewBox="0 0 178 16" aria-hidden="true">
      <line x1="0" y1="8" x2="81" y2="8" stroke="var(--accent)" stroke-width="1"/>
      <line x1="97" y1="8" x2="178" y2="8" stroke="var(--accent)" stroke-width="1"/>
      <circle cx="89" cy="8" r="5" fill="var(--accent)"/>
      <circle cx="89" cy="8" r="2" fill="#fff"/>
    </svg>
    <p class="welcome-text">Sed ut perspiciatis unde omnis iste natus error sit voluptatem accusantium doloremque laudantium, totam rem aperiam, eaque ipsa quae ab illo inventore veritatis et quasi architecto beatae vitae dicta sunt explicabo. Nemo enim ipsam voluptatem quia voluptas sit aspernatur aut odit aut fugit, sed quia consequuntur magni dolores eos qui ratione voluptatem sequi nesciunt. Neque porro quisquam est, qui dolorem ipsum quia dolor sit amet, consectetur, adipisci velit</p>
    <div class="btn-more">READ MORE</div>
  </section>

  <h2 class="work-title">OUR WORK</h2>
  <article class="work-card" style="left:73px">
    <div class="render" role="img" aria-label="Rendering of a two-storey white house exterior" style="background:linear-gradient(#c9ccd0,#e6e6e4 60%,#9aa197)"></div>
    <p>Lorem ipsum dolor sit amet, consectetur adipisicing elit, sed do eiusmod</p>
  </article>
  <article class="work-card" style="left:262px">
    <div class="render" role="img" aria-label="Sketch rendering of a living room with fireplace and sofa" style="background:linear-gradient(#eeeeec,#cfcfcd)"></div>
    <p>Lorem ipsum dolor sit amet, consectetur adipisicing elit, sed do eiusmod</p>
  </article>
  <article class="work-card" style="left:452px">
    <div class="render" role="img" aria-label="3D rendering of a kitchen island with dark countertop" style="background:linear-gradient(#d8d8d6,#a9a9a7 60%,#6e6e6e)"></div>
    <p>Lorem ipsum dolor sit amet, consectetur adipisicing elit, sed do eiusmod</p>
  </article>
  <article class="work-card" style="left:641px">
    <div class="render" role="img" aria-label="Hand-coloured furniture floor plan" style="background:linear-gradient(#f1ede6,#e6dccd)"></div>
    <p>Lorem ipsum dolor sit amet, consectetur adipisicing elit, sed do eiusmod</p>
  </article>

  <footer class="site-footer">
    <div class="social" aria-label="Social links"><span></span><span></span><span></span><span></span><span></span></div>
    <div class="footer-links"><a>Home</a><i>/</i><a>Process</a><i>/</i><a>About us</a><i>/</i><a>Example Works</a><i>/</i><a>Client Corner</a><i>/</i><a>Contact Us</a></div>
    <div class="copyright">Copyright @ 2017 Nora Whitfield Interior Design. All Rights Reserved.</div>
  </footer>
</div>
</body>
</html>
```